Blog Design for global news commentary

Need a very simple blog template (see attachment, Frontpage) that includes entries and ability to upload photos/video. Tabs are not needed (See Marlow Tearoom Provincial blog for sort of what I am going for but a lot less cluttered). A section that can access old entries is needed as well as a "contact me" tab. The format should be very simple. An entry and section for comments, new entry, section for comments etc. comments sections should be able to be monitored by me. With the ability for readers to contribute via quidlane. The look and feel should be sophisticated and should target an educated global audience. The blog is all about commenting on global news around the world. For example, a news article could be photographed and then commented on. Type face should be simple, clean and 1930's style. See Harbor Ledger magazine for looks and feel. If viewers wish to contribute they can make donations via quidlane on the site. Once the template is competed it should be very easy for me to update and work with and handed over to a web hosting service. I own the domain name which I want to use. It would be best to use an existing template eg wordpress. So in simple terms need a wordpress template adapted for this blog idea. Not sure what coded vs. uncoded means. But the overall objective is very simple. Template should be clean, no design elements other than the name of the blog.

Target Market(s)

Educated people from around the world interested in current events

Industry/Entity Type

News

Number of Pages Required

2 page

Other font styles liked:
• Upper East Side

Colors
0255a3
1b1b1b
5c5c5c

Requirements
Must have
• This is a blog so it should have all the standard features including daily updates, photo/video upload, comments that can be monitored by me, quidlane donation link. It should be easy for me to use and handle once completed and delivered to web host. It must have a simple, elegant look and feel. I have chose Serif font style but recommend a 1930's Art Deco - clean, unfussy type face. Type face Upper East Side is what I am looking for
Nice to have
• The look must be simple and no pictures, design elements or logos. Clean and crisp
Should not have
• Any pictures for illustrations as part of the overall design

```html
<!DOCTYPE html>
<html lang="en">
<head>
<meta charset="utf-8">
<title>Meridian — Global News Commentary</title>
<link rel="stylesheet" href="https://fonts.googleapis.com/css2?family=Open+Sans:wght@400;600;700&family=Playfair+Display:wght@400;700&display=swap">
<style>
:root{
  --blue:#0255a3;
  --blue-dark:#01427f;
  --ink:#1b1b1b;
  --grey:#5c5c5c;
  --page:#eeeff1;
  --card:#ffffff;
  --line:#d9dbdf;
  --footer:#2f3236;
  --footer-bottom:#222427;
  --gold:#f6c233;
}
*{box-sizing:border-box;margin:0;padding:0}
html,body{width:1200px;height:2492px;overflow:hidden}
body{font-family:"Open Sans",Arial,sans-serif;color:var(--grey);background:var(--page);position:relative;font-size:12px}
.abs{position:absolute}

/* header */
.site-header{left:0;top:0;width:1200px;height:112px;background:var(--blue)}
.brand{left:88px;top:30px;font-size:40px;color:#fff;font-weight:400;font-family:"Playfair Display",Georgia,serif}
.main-nav{right:200px;top:44px;display:flex;gap:26px}
.main-nav a{color:#fff;text-decoration:none;font-size:13px;font-weight:600;letter-spacing:.5px}
.search-icon{left:1018px;top:42px}
.donate-btn{left:1046px;top:36px;width:68px;height:36px;background:var(--gold);border-radius:4px;color:var(--blue-dark);font-weight:700;font-size:12px;display:flex;align-items:center;justify-content:center;white-space:nowrap}

/* hero */
.hero{left:0;top:112px;width:1200px;height:568px;background:linear-gradient(135deg,#8d8f94 0%,#c9ccd1 40%,#e8e9eb 60%,#9a9ca1 100%)}
.hero-caption{left:88px;top:420px;width:520px;height:136px;background:rgba(20,20,20,.68);padding:24px 26px}
.hero-caption .kicker{font-family:"Playfair Display",Georgia,serif;color:#fff;font-size:20px;letter-spacing:1px;text-transform:uppercase;white-space:nowrap}
.hero-caption .lead{font-family:"Playfair Display",Georgia,serif;color:#fff;font-size:28px;line-height:38px;margin-top:10px;white-space:nowrap}
.slider-dots{left:1014px;top:640px;display:flex;gap:8px}
.slider-dots span{width:9px;height:9px;border-radius:50%;background:#fff;opacity:.6}
.slider-dots span:first-child{opacity:1}

/* featured videos */
.video-thumb{top:720px;width:336px;height:192px;border:4px solid #fff;box-shadow:0 1px 3px rgba(0,0,0,.2)}
.play{position:absolute;left:50%;top:50%;width:50px;height:50px;margin:-25px 0 0 -25px}
.feature-title{top:944px;width:336px;font-size:13px;font-weight:700;color:var(--ink)}
.feature-text{top:970px;width:320px;font-size:11.5px;line-height:17px}
.divider{left:88px;top:1072px;width:1024px;height:1px;background:var(--line)}

/* news */
.section-title{left:88px;top:1112px;font-size:15px;font-weight:700;color:var(--blue);letter-spacing:.5px}
.section-title::after{content:"";display:block;width:60px;height:2px;background:var(--blue);margin-top:6px}
.article-card{left:88px;width:732px;height:300px;background:var(--card);border:1px solid var(--line)}
.article-photo{left:22px;top:24px;width:228px;height:160px}
.article-title{left:270px;top:18px;width:440px;font-size:15px;font-weight:700;color:var(--blue);line-height:21px}
.article-meta{left:270px;top:70px;font-size:11px;color:var(--grey)}
.article-meta b{color:var(--ink);font-weight:600}
.article-text{left:270px;top:94px;width:440px;font-size:11.5px;line-height:17px}
.read-more{left:270px;top:154px;width:88px;height:24px;background:var(--blue);color:#fff;font-size:11px;font-weight:600;border-radius:3px;display:flex;align-items:center;justify-content:center}
.share-pill{top:156px;height:20px;border:1px solid var(--line);border-radius:3px;background:#f6f7f8}
.comment-row{left:22px;top:232px;width:688px;height:34px;border:1px solid var(--line);border-radius:3px}
.comment-row span{position:absolute;left:12px;top:9px;font-size:11px;color:#999}
.send-btn{right:6px;top:5px;width:60px;height:22px;background:var(--blue);color:#fff;border-radius:3px;font-size:11px;font-weight:600;display:flex;align-items:center;justify-content:center}

/* sidebar */
.widget{left:832px;width:280px;background:var(--card);border:1px solid var(--line)}
.widget-head{height:40px;padding:12px 16px;font-size:13px;font-weight:700;color:var(--blue);border-bottom:1px solid var(--line)}
.widget-head.solid{background:var(--blue);color:#fff;border:0}
.popular-item{display:flex;gap:12px;padding:14px 16px 0}
.popular-thumb{width:70px;height:48px;flex:none;background:linear-gradient(135deg,#9fb6cc,#d5dde6)}
.popular-item p{font-size:11px;line-height:15px}
.popular-item p b{display:block;color:var(--blue);font-weight:600;font-size:12px}
.archive-list{list-style:none;padding:10px 16px}
.archive-list li{display:flex;align-items:center;gap:10px;height:32px;font-size:12px;color:var(--ink);border-bottom:1px solid #eef0f2}
.archive-list li::before{content:"";width:10px;height:10px;border-radius:50%;border:2px solid var(--blue)}
.side-video{left:832px;top:1840px;width:280px;height:288px;border:4px solid #fff;box-shadow:0 1px 3px rgba(0,0,0,.2)}

/* footer */
.site-footer{left:0;top:2200px;width:1200px;height:200px;background:var(--footer)}
.footer-col{top:2232px}
.footer-col h4{font-size:12px;font-weight:700;color:#fff;margin-bottom:14px;letter-spacing:.5px}
.footer-col p{font-size:11px;color:#b7bbc1;line-height:20px}
.footer-bottom{left:0;top:2400px;width:1200px;height:92px;background:var(--footer-bottom)}
.legal{left:88px;top:2428px;font-size:11px;color:#b7bbc1;line-height:19px}
.social{top:2428px;width:28px;height:28px;background:var(--blue);border-radius:3px}
</style>
</head>
<body>

<header class="site-header abs">
  <div class="brand abs">Meridian</div>
  <nav class="main-nav abs">
    <a href="#">HOME</a><a href="#">ABOUT US</a><a href="#">SERVICE</a><a href="#">NEWS</a><a href="#">BLOG</a><a href="#">CONTACTS</a>
  </nav>
  <svg class="search-icon abs" width="20" height="22" viewBox="0 0 20 22"><circle cx="8" cy="8" r="6" fill="none" stroke="#fff" stroke-width="2.5"/><line x1="12.5" y1="12.5" x2="18" y2="19" stroke="#fff" stroke-width="3" stroke-linecap="round"/></svg>
  <div class="donate-btn abs">quidlane</div>
</header>

<section class="hero abs" role="img" aria-label="Photo of colleagues around a desk reviewing printed charts with coffee cups"></section>
<div class="hero-caption abs">
  <div class="kicker">Global news around the world</div>
  <div class="lead">Lorem Ipsum is simply dummy text</div>
</div>
<div class="slider-dots abs"><span></span><span></span><span></span><span></span><span></span></div>

<div class="video-thumb abs" style="left:88px;background:linear-gradient(135deg,#9cb8d4,#e3ebf3)" role="img" aria-label="Video still of a person writing">
  <svg class="play" viewBox="0 0 50 50"><circle cx="25" cy="25" r="24" fill="rgba(0,0,0,.55)"/><path d="M20 15 L36 25 L20 35Z" fill="#fff"/></svg>
</div>
<div class="video-thumb abs" style="left:432px;background:linear-gradient(135deg,#8a7c6c,#d6cbbd)" role="img" aria-label="Video still of a laptop on a wooden desk">
  <svg class="play" viewBox="0 0 50 50"><circle cx="25" cy="25" r="24" fill="rgba(0,0,0,.55)"/><path d="M20 15 L36 25 L20 35Z" fill="#fff"/></svg>
</div>
<div class="video-thumb abs" style="left:776px;background:linear-gradient(135deg,#2c4f86,#8fb0d8)" role="img" aria-label="Video still of a presenter in front of a screen">
  <svg class="play" viewBox="0 0 50 50"><circle cx="25" cy="25" r="24" fill="rgba(0,0,0,.55)"/><path d="M20 15 L36 25 L20 35Z" fill="#fff"/></svg>
</div>
<div class="feature-title abs" style="left:88px">LOREM IPSUM IS SIMPLY DUMMY</div>
<div class="feature-title abs" style="left:432px">LOREM IPSUM IS SIMPLY DUMMY</div>
<div class="feature-title abs" style="left:776px">LOREM IPSUM IS SIMPLY DUMMY</div>
<p class="feature-text abs" style="left:88px">Lorem Ipsum has been the industry's standard dummy text ever since the 1500s, when an</p>
<p class="feature-text abs" style="left:432px">Lorem Ipsum has been the industry's standard dummy text ever since the 1500s, when an</p>
<p class="feature-text abs" style="left:776px">Lorem Ipsum has been the industry's standard dummy text ever since the 1500s, when an</p>

<div class="divider abs"></div>
<h2 class="section-title abs">NEWS ARTICLE</h2>

<article class="article-card abs" style="top:1160px">
  <div class="article-photo abs" style="background:linear-gradient(135deg,#1c2f4a,#5a7fa8)" role="img" aria-label="Photo of hands holding a small globe"></div>
  <h3 class="article-title abs">Maecenas vel consequat dolor, id ultrices dolor. Integer dignissim magna.</h3>
  <div class="article-meta abs">Post by : <b>admin</b> &nbsp;|&nbsp; Post on : October 1, 2015 &nbsp; at 10:15 a.m</div>
  <p class="article-text abs">Sed id tincidunt arcu. Maecenas eget nibh sit amet dapibus dictum. Vestibulum ante ipsum primis in faucibus orci luctus et ultrices posuere cubilia Curae. In hac habitasse platea dictumst.</p>
  <div class="read-more abs">Read more</div>
  <div class="share-pill abs" style="left:372px;width:50px"></div>
  <div class="share-pill abs" style="left:430px;width:40px"></div>
  <div class="share-pill abs" style="left:478px;width:40px"></div>
  <div class="share-pill abs" style="left:540px;width:30px"></div>
  <div class="comment-row abs"><span>Add a comment on a subjective...</span><div class="send-btn abs">Send</div></div>
</article>

<article class="article-card abs" style="top:1480px">
  <div class="article-photo abs" style="background:linear-gradient(135deg,#0f2238,#3a6a9a)" role="img" aria-label="Photo of a tablet showing a news page"></div>
  <h3 class="article-title abs">Maecenas vel consequat dolor, id ultrices dolor. Integer dignissim magna.</h3>
  <div class="article-meta abs">Post by : <b>admin</b> &nbsp;|&nbsp; Post on : October 1, 2015 &nbsp; at 10:15 a.m</div>
  <p class="article-text abs">Sed id tincidunt arcu. Maecenas eget nibh sit amet dapibus dictum. Vestibulum ante ipsum primis in faucibus orci luctus et ultrices posuere cubilia Curae. In hac habitasse platea dictumst.</p>
  <div class="read-more abs">Read more</div>
  <div class="share-pill abs" style="left:372px;width:50px"></div>
  <div class="share-pill abs" style="left:430px;width:40px"></div>
  <div class="share-pill abs" style="left:478px;width:40px"></div>
  <div class="share-pill abs" style="left:540px;width:30px"></div>
  <div class="comment-row abs"><span>Add a comment on a subjective...</span><div class="send-btn abs">Send</div></div>
</article>

<article class="article-card abs" style="top:1808px">
  <div class="article-photo abs" style="background:linear-gradient(135deg,#a58a6a,#e3d6c3)" role="img" aria-label="Photo of a desk with newspapers and a laptop"></div>
  <h3 class="article-title abs">Maecenas vel consequat dolor, id ultrices dolor. Integer dignissim magna.</h3>
  <div class="article-meta abs">Post by : <b>admin</b> &nbsp;|&nbsp; Post on : October 1, 2015 &nbsp; at 10:15 a.m</div>
  <p class="article-text abs">Sed id tincidunt arcu. Maecenas eget nibh sit amet dapibus dictum. Vestibulum ante ipsum primis in faucibus orci luctus et ultrices posuere cubilia Curae. In hac habitasse platea dictumst.</p>
  <div class="read-more abs">Read more</div>
  <div class="share-pill abs" style="left:372px;width:50px"></div>
  <div class="share-pill abs" style="left:430px;width:40px"></div>
  <div class="share-pill abs" style="left:478px;width:40px"></div>
  <div class="share-pill abs" style="left:540px;width:30px"></div>
  <div class="comment-row abs"><span>Add a comment on a subjective...</span><div class="send-btn abs">Send</div></div>
</article>

<aside class="widget abs" style="top:1160px;height:372px">
  <div class="widget-head">POPULAR POSTS</div>
  <div class="popular-item"><div class="popular-thumb" role="img" aria-label="Post thumbnail"></div><p><b>This is a sample Post 1</b>Lorem ipsum dolor sit amet, consectetur</p></div>
  <div class="popular-item"><div class="popular-thumb" role="img" aria-label="Post thumbnail"></div><p><b>This is a sample Post 2</b>Lorem ipsum dolor sit amet, consectetur</p></div>
  <div class="popular-item"><div class="popular-thumb" role="img" aria-label="Post thumbnail"></div><p><b>This is a sample Post 3</b>Lorem ipsum dolor sit amet, consectetur</p></div>
  <div class="popular-item"><div class="popular-thumb" role="img" aria-label="Post thumbnail"></div><p><b>This is a sample Post 4</b>Lorem ipsum dolor sit amet, consectetur</p></div>
</aside>

<aside class="widget abs" style="top:1552px;height:268px">
  <div class="widget-head solid">ARCHIVES</div>
  <ul class="archive-list">
    <li>April 2015</li><li>March 2015</li><li>February 2015</li><li>January 2015</li><li>September 2014</li><li>June 2014</li>
  </ul>
</aside>

<div class="side-video abs" style="background:linear-gradient(135deg,#6d6f74,#c2c4c8)" role="img" aria-label="Video still of a meeting around a table">
  <svg class="play" viewBox="0 0 50 50"><circle cx="25" cy="25" r="24" fill="rgba(0,0,0,.55)"/><path d="M20 15 L36 25 L20 35Z" fill="#fff"/></svg>
</div>

<footer class="site-footer abs"></footer>
<div class="footer-col abs" style="left:88px"><h4>LINK</h4><p>Home<br>About us<br>Presentation</p></div>
<div class="footer-col abs" style="left:264px"><h4>SPECIALISTS</h4><p>Services<br>Showcases<br>Technology</p></div>
<div class="footer-col abs" style="left:464px"><h4>ADVICE</h4><p>FAQs<br>Support</p></div>
<div class="footer-col abs" style="left:648px"><h4>AGENCIES</h4><p>Sign Up<br>Forums<br>Promotions</p></div>
<div class="footer-col abs" style="left:828px"><h4>CONTACT US</h4><p>24 Quay Lane, 4021 Harbourside<br>Phone: +00 21 555 0192<br>Email: desk@meridian.example</p></div>

<div class="footer-bottom abs"></div>
<p class="legal abs">Privacy Policy &nbsp;|&nbsp; Terms of Use &nbsp;|&nbsp; Sitemap<br>Copyright © 2015. All Rights Reserved</p>
<div class="social abs" style="left:968px"></div>
<div class="social abs" style="left:1002px"></div>
<div class="social abs" style="left:1036px"></div>
<div class="social abs" style="left:1070px"></div>

</body>
</html>
```